New Business Card Design Project

I need a design for business cards, i am an electrical business called "Corvane Electrical and Communications" i need the cards to be double sided with the company logo on the back (attached) the front needs to say my company name, web site, email address, telephone number, and ABN number and electrical license number. I am open to different arrangements of the information but would like the background to be incorporating something electrical or something that looks smart. open to all additional ideas also.

The company colours are orange and grey see logo attached.

Business Name: Corvane Electrical and Communications
Website: corvaneelectricalandcomms.example.com.au
Email: brent@corvaneelectricalandcomms.example.com.au
Telephone(mobile): 0481209736
ABN: 71208349162
Lic No: 418273D

Target Market(s)

Business entities, Project Managers, Accounts, Clients

Industry/Entity Type

Electrician

Contact Information for Business Card

I need a design for business cards, i am an electrical business called "Corvane Electrical and Communications" i need the cards to be double sided with the company logo on the back (attached) the front needs to say my company name

Font styles to use
Serif
Sans Serif

Colors
f37122
5c5c5c

Requirements
Must have
• Must have the Logo on the back open to different ways of it being on the back but had in mind to keep it central but again open to other options
Nice to have
• A real modern cool background that is eye catching yet contemporary
Should not have
• No backgrounds of a light bulb or plug or anything like that

```html
<!DOCTYPE html>
<html lang="en">
<head>
<meta charset="utf-8">
<title>Corvane Electrical and Communications – Business Cards</title>
<link rel="stylesheet" href="https://fonts.googleapis.com/css2?family=Exo+2:wght@400;600;700&display=swap">
<style>
  :root {
    --orange: #f7a81b;
    --orange-deep: #f08f10;
    --grey-dark: #4a4a4c;
    --grey-mid: #6b6b6d;
    --grey-light: #c9c9c9;
    --white: #ffffff;
    --stage: #ecebe8;
  }
  * { box-sizing: border-box; margin: 0; padding: 0; }
  html, body {
    width: 1200px; height: 843px; overflow: hidden;
    background: var(--stage);
    font-family: "Exo 2", sans-serif;
  }
  .canvas {
    position: relative; width: 1200px; height: 843px;
  }
  .card {
    position: absolute; top: 256px;
    width: 540px; height: 330px;
    border-radius: 22px; overflow: hidden;
    box-shadow: 0 10px 28px rgba(0,0,0,.22);
  }
  .card-back { left: 45px; background: var(--white); }
  .card-front {
    left: 615px;
    background: linear-gradient(135deg, var(--grey-mid) 0%, var(--grey-dark) 100%);
  }
  .card-art { position: absolute; inset: 0; width: 100%; height: 100%; }

  /* back side */
  .back-brand {
    position: absolute; left: 0; right: 0; top: 178px;
    text-align: center; color: var(--white); font-weight: 600;
  }
  .back-brand .brand-name { font-size: 58px; letter-spacing: 6px; line-height: 1; text-transform: uppercase; }
  .back-brand .brand-line { font-size: 15px; letter-spacing: 2px; text-transform: uppercase; margin-top: 4px; }
  .back-web {
    position: absolute; left: 0; right: 0; bottom: 22px;
    text-align: center; color: var(--white); font-size: 15px; letter-spacing: 1px;
  }

  /* front side */
  .front-brand {
    position: absolute; right: 34px; top: 62px; text-align: right;
    color: var(--white); font-weight: 600;
  }
  .front-brand .brand-name { font-size: 40px; letter-spacing: 4px; line-height: 1; text-transform: uppercase; }
  .front-brand .brand-line { font-size: 11px; letter-spacing: 1px; text-transform: uppercase; margin-top: 4px; }

  .contact {
    position: absolute; left: 40px; top: 84px; color: var(--white);
    font-size: 15px; line-height: 1.45;
  }
  .contact .person-name { color: var(--orange); font-weight: 700; font-size: 22px; letter-spacing: 1px; line-height: 1.2; }
  .contact .person-role { margin-bottom: 8px; }
  .contact-row { display: flex; align-items: center; gap: 8px; }
  .contact-row svg { width: 13px; height: 13px; flex: none; }
</style>
</head>
<body>
<main class="canvas">

  <section class="card card-back" aria-label="Card back">
    <svg class="card-art" viewBox="0 0 540 330" preserveAspectRatio="none" aria-hidden="true">
      <defs>
        <linearGradient id="backBand" x1="0" y1="0" x2="0" y2="1">
          <stop offset="0" stop-color="var(--orange)"/>
          <stop offset="1" stop-color="var(--orange-deep)"/>
        </linearGradient>
      </defs>
      <path d="M0 130 C 140 110, 380 150, 540 118 L540 330 L0 330 Z" fill="url(#backBand)"/>
      <path d="M0 130 C 140 110, 380 150, 540 118" fill="none" stroke="var(--grey-mid)" stroke-width="6"/>
    </svg>
    <div class="back-brand">
      <div class="brand-name">Corvane</div>
      <div class="brand-line">Electrical &amp; Communications</div>
    </div>
    <div class="back-web">www.corvaneelectricalandcomms.example.com.au</div>
  </section>

  <section class="card card-front" aria-label="Card front">
    <svg class="card-art" viewBox="0 0 540 330" preserveAspectRatio="none" aria-hidden="true">
      <path d="M0 0 L120 0 C 60 10, 18 40, 0 78 Z" fill="var(--white)"/>
      <path d="M0 82 C 30 30, 110 6, 260 2" fill="none" stroke="var(--orange)" stroke-width="4"/>
      <path d="M540 200 C 500 270, 420 318, 340 330 L540 330 Z" fill="var(--grey-light)"/>
      <path d="M540 188 C 500 270, 400 322, 300 330" fill="none" stroke="var(--orange)" stroke-width="4"/>
    </svg>

    <div class="front-brand">
      <div class="brand-name">Corvane</div>
      <div class="brand-line">Electrical &amp; Communications</div>
    </div>

    <div class="contact">
      <div class="person-name">Darren Holt</div>
      <div class="person-role">CEO/Founder</div>
      <div>ABN: 71208349162</div>
      <div>Lic No: 418273D</div>
      <div class="contact-row">
        <svg viewBox="0 0 12 12" aria-hidden="true"><rect x="3" y="0.5" width="6" height="11" rx="1.2" fill="none" stroke="var(--orange)" stroke-width="1.2"/><circle cx="6" cy="9.5" r="0.8" fill="var(--orange)"/></svg>
        <span>0481209736</span>
      </div>
      <div class="contact-row">
        <svg viewBox="0 0 12 12" aria-hidden="true"><rect x="0.5" y="2" width="11" height="8" fill="var(--orange)"/><path d="M0.5 2 L6 7 L11.5 2" fill="none" stroke="var(--grey-dark)" stroke-width="1"/></svg>
        <span>brent@corvaneelectricalandcomms.example.com.au</span>
      </div>
      <div class="contact-row">
        <svg viewBox="0 0 12 12" aria-hidden="true"><circle cx="6" cy="6" r="5.5" fill="var(--orange)"/><path d="M0.5 6 H11.5 M6 0.5 C3 3.5 3 8.5 6 11.5 M6 0.5 C9 3.5 9 8.5 6 11.5" fill="none" stroke="var(--grey-dark)" stroke-width="0.8"/></svg>
        <span>corvaneelectricalandcomms.example.com.au</span>
      </div>
    </div>
  </section>

</main>
</body>
</html>
```